K&T Smokehouse Website Design Project

K& T Smokehouse AsaderÃa is a fast-casual restaurant that specializes in southern culture, soul food, baby back ribs and bourbon whiskey.
We need a functional and user friendly website design for our customers to be able to explore our menu options, learn about our culture, as well as be able to place and pay for online orders that can be picked up at the nearest restaurant. Benchmarks for our website are www.crumbvalebakery.com, www.zestoragrill.com and www.marisolkitchen.com
The site design should also serve as an initial point of contact for prospective franchisees to dig and learn about the brand and business opportunity.
We want customers (consumers and potential franchisees) to be able to experience FIRST THE FOOD, but also the style and culture of our restaurants via the website design. Key elements for this are: soul food (Warm Your Heart), southern culture, friendly service, bluegrass/folk music, bourbon/moonshine/Tennessee whisky, modern butcher-shop design as well as industrial, wood, modern rustic, organic elements. (see restaurant images of tile, concrete, vintage scales, green wall, etc)
We want the website to provide a good overall brand image and also drive participation and sales by via images of our food, by these images being at front and center of the website design. See benchmark websites (Crumbvale, Marisol Kitchen, Zestora) for good examples of this.
Other elements to take under consideration for the website design are:
* Illustrative but simple menu
* Hacer un pedido (order online), Loyalty Program and Franquicias sections should have different, separate and easy to see buttons in the homepage.
* Simple, but modern functionality overall for the website.
* Respect colors and elements of the brand (attached some photos and examples)
* Brand Typography included (NAMES OF TYPOGRAPHY: BEBAS, SONGBIRD, CANTER & VAST SHADOW)
Minimum Deliverables: Home Page, Menu and Order Online. 3 pages total.
• More examples can be found at: www.facebook.com/ktsmokehouseasaderia
• Website architecture / Site Map ATTACHED
* More design elements attached.
* Screenshots of some good elements to take under consideration for website functionality and design.
- BEBAS, SONGBRID, CANTER & VAST SHADOW

```html
<!DOCTYPE html>
<html lang="es">
<head>
<meta charset="utf-8">
<title>K&amp;T Smokehouse — Menu</title>
<link rel="stylesheet" href="https://fonts.googleapis.com/css2?family=Oswald:wght@300;400;500&family=Abel&family=Bebas+Neue&display=swap">
<style>
:root{
  --slate:#5c5c5e;
  --slate-dark:#4a4a4c;
  --ink:#0b0b0b;
  --mustard:#d4a62a;
  --brick:#b8272a;
  --brick-soft:rgba(178,34,38,.82);
  --blush:#f4b4b0;
  --paper:#f1eee6;
  --white:#ffffff;
  --muted:#d8d8d8;
}
*{margin:0;padding:0;box-sizing:border-box}
html,body{width:1186px;height:1200px;overflow:hidden}
body{background:var(--slate);font-family:"Oswald",sans-serif;color:var(--white);position:relative}
.abs{position:absolute}

/* header */
.brand{left:68px;top:0;width:234px;height:160px;background:var(--mustard);display:flex;align-items:center;justify-content:center}
.brand-name{font-family:"Oswald",sans-serif;font-weight:500;font-size:24px;color:var(--ink);text-align:center;line-height:1.1;letter-spacing:1px}
.account{left:818px;top:17px;width:176px;height:30px;background:var(--paper);color:#333;font-size:14px;display:flex;align-items:center;justify-content:center;gap:8px;font-weight:300}
.account .sep{width:1px;height:14px;background:#999}
.social{display:flex;gap:8px}
.social span{width:28px;height:28px;border-radius:50%;background:#e9e9e9;display:block}
.social.top{left:1014px;top:18px}
.cta{top:83px;height:42px;display:flex;align-items:center;justify-content:center;gap:10px;font-size:15px;color:var(--white);text-transform:uppercase;font-weight:400}
.cta svg{flex:none}
.cta-order{left:512px;width:188px;background:var(--mustard)}
.cta-catering{left:714px;width:193px;background:var(--brick)}
.cta-loyalty{left:921px;width:190px;background:var(--blush)}
.nav{left:0;top:145px;width:1186px;height:65px;background:var(--ink);display:flex;justify-content:center;align-items:center;gap:40px;font-size:17px;text-transform:uppercase;font-weight:400}
.nav .active{color:var(--mustard)}

/* hero */
.hero{left:0;top:208px;width:1186px;height:703px;background:linear-gradient(90deg,#6b4a30 0%,#8a5a34 30%,#a4542a 45%,#7a4a2e 60%,#6a4530 100%)}
.menu-list{left:74px;top:267px;width:238px}
.menu-head{background:var(--brick-soft);height:77px;text-align:center;padding-top:17px;text-transform:uppercase}
.menu-head b{display:block;font-weight:500;font-size:18px;line-height:1.1}
.menu-head small{font-size:11px;font-weight:400}
.menu-item{height:60px;margin-top:9px;background:var(--brick-soft);font-family:"Abel",sans-serif;font-size:21px;display:flex;align-items:center;justify-content:center}
.menu-item.current{background:rgba(255,255,255,.88);color:var(--brick);margin-top:1px}
.menu-item.cal{font-family:"Oswald",sans-serif;font-size:18px;text-transform:uppercase;height:76px}
.submenu{left:332px;top:311px;width:238px;height:197px;background:rgba(255,255,255,.85);color:#222;font-family:"Abel",sans-serif;font-size:21px;text-align:center;padding:24px 14px 0}
.submenu li{list-style:none;padding:0 0 10px;margin-bottom:12px;border-bottom:1px dashed #999;line-height:1.15}
.submenu li:last-child{border:none}

/* footer */
.divider{left:143px;top:935px;width:900px;height:1px;background:#8a8a8a}
.divider-mark{left:565px;top:929px;width:56px;height:12px;background:var(--slate);display:flex;justify-content:center;align-items:center}
.divider-mark i{width:40px;height:2px;background:#aaa;display:block}
.amenities{left:76px;top:1040px;font-size:14px;font-weight:300;line-height:31px}
.amenities div{display:flex;align-items:center;gap:8px}
.newsletter{left:249px;top:980px;width:662px;height:163px;border:1px dashed #bbb;background:var(--slate-dark)}
.jars{left:14px;top:24px;width:150px;height:118px;background:linear-gradient(180deg,#3a3d48,#8a6a3a)}
.keep{left:160px;top:50px;width:128px;font-family:"Bebas Neue",sans-serif;font-size:27px;line-height:30px;letter-spacing:0;white-space:nowrap;color:var(--white)}
.blurb{left:302px;top:52px;width:282px;font-size:12px;font-weight:300;line-height:1.3}
.signup{left:202px;top:95px;display:flex}
.signup .field{width:272px;height:33px;background:var(--white);color:#777;font-size:13px;padding:8px 10px;font-weight:300}
.signup .btn{width:73px;height:33px;background:var(--mustard);color:var(--ink);font-size:15px;display:flex;align-items:center;justify-content:center}
.follow{left:940px;top:1022px;font-size:14px}
.follow .social{margin-top:10px}
.legal{left:0;top:1166px;width:1186px;text-align:center;font-size:13px;font-weight:300;display:flex;justify-content:center;gap:14px}
</style>
</head>
<body>
<header>
  <div class="abs brand"><div class="brand-name">K&amp;T SMOKEHOUSE<br>ASADERIA</div></div>
  <div class="abs account">Sign In <span class="sep"></span> Join Now</div>
  <div class="abs social top"><span></span><span></span><span></span></div>
  <a class="abs cta cta-order"><svg width="20" height="22" viewBox="0 0 20 22"><rect x="2" y="1" width="16" height="20" fill="none" stroke="#fff" stroke-width="2"/><path d="M6 7h8M6 11h8M6 15h5" stroke="#fff" stroke-width="2"/></svg>Order Online</a>
  <a class="abs cta cta-catering"><svg width="24" height="22" viewBox="0 0 24 22"><path d="M3 15a9 9 0 0 1 18 0z" fill="#fff"/><rect x="1" y="16" width="22" height="3" fill="#fff"/></svg>Order Catering</a>
  <a class="abs cta cta-loyalty"><svg width="26" height="20" viewBox="0 0 26 20"><path d="M2 10l6-6 5 4 5-4 6 6-11 8z" fill="#fff"/></svg>Loyalty Program</a>
  <nav class="abs nav"><span>Nuestra Historia</span><span class="active">Menu</span><span>Restaurantes</span><span>Franquicias</span><span>Escríbenos</span><span>Facturación</span></nav>
</header>

<main>
  <div class="abs hero" role="img" aria-label="Photo of red, orange and yellow chili peppers beside a wooden spoon of ground chili on a rustic wood table"></div>
  <aside class="abs menu-list">
    <div class="menu-head"><b>Download Menu</b><small>Menu options may vary by location</small></div>
    <div class="menu-item current">Costillas y mas</div>
    <div class="menu-item">Guarniciones</div>
    <div class="menu-item">Bebidas</div>
    <div class="menu-item">Combos</div>
    <div class="menu-item">Paquetes</div>
    <div class="menu-item">Salsas</div>
    <div class="menu-item cal">500 Calorie Menu</div>
  </aside>
  <ul class="abs submenu">
    <li>Full Rack</li>
    <li>Medio Rack</li>
    <li>Sandwich de Puerco Jalado</li>
  </ul>
</main>

<footer>
  <div class="abs divider"></div>
  <div class="abs divider-mark"><i></i></div>
  <div class="abs amenities">
    <div><svg width="16" height="12" viewBox="0 0 16 12"><path d="M1 4a10 10 0 0 1 14 0M4 7a6 6 0 0 1 8 0" fill="none" stroke="#fff" stroke-width="1.6"/><circle cx="8" cy="10" r="1.6" fill="#fff"/></svg>Free Wi-Fi</div>
    <div><svg width="20" height="14" viewBox="0 0 20 14"><circle cx="10" cy="4" r="3" fill="#fff"/><circle cx="3.5" cy="6" r="2.2" fill="#fff"/><circle cx="16.5" cy="6" r="2.2" fill="#fff"/><path d="M4 14a6 5 0 0 1 12 0z" fill="#fff"/></svg>Community Rooms</div>
  </div>
  <section class="abs newsletter">
    <div class="abs jars" role="img" aria-label="Photo of two whiskey jars on a wooden serving board"></div>
    <div class="abs keep">Keep in Touch</div>
    <p class="abs blurb">Exclusive offers, great video's and recipes - you'll love getting emails from K&amp;T Smokehouse.</p>
    <div class="abs signup"><div class="field">Enter your email address...</div><div class="btn">Sign up</div></div>
  </section>
  <div class="abs follow">Come Be Social With Us:<div class="social"><span></span><span></span><span></span></div></div>
  <div class="abs legal"><span>©2015 K&amp;T Smokehouse</span>|<span>Contact Us</span>|<span>Terms of Us</span>|<span>Privacy Policy</span>|<span>Sitemap</span></div>
</footer>
</body>
</html>
```